Harbourline Physiotherapy business card design

We need a fresh, new business card design for our physiotherapy clinic Harbourline Physiotherapy

Will attach logo soon we had logo designed from our last project

Industry/Entity Type

Physical Therapy

Contact Information for Business Card

On front
Needs our logo, contact details:
58 Wexley Lane Marrowdale NSW 2784
Ph/f: 02 9481 2057
info@harbourlinephysio.example.com.au

Requirements
Must have
• On the back of the card needs to have area to write down follow up appointments
• On front
• Needs our logo
• The colours have to be the colours in our logo which are: sky blue, black and white
• Font to be same as our logo please
• We want the card to look simple, not too cluttered but to the point
Should not have
• We don't need any extra pictures other than our logo

```html
<!DOCTYPE html>
<html lang="en">
<head>
<meta charset="utf-8">
<title>Harbourline Physiotherapy – Business Card</title>
<link href="https://fonts.googleapis.com/css2?family=Open+Sans:wght@400;600;700&display=swap" rel="stylesheet">
<style>
  :root {
    --page-bg: #e9e6e1;
    --card-white: #ffffff;
    --card-shade: #e4e6ea;
    --brand-blue: #1d5fb8;
    --sky-blue: #2f8fd8;
    --ink: #3a3a3a;
    --rule: #5b8fd3;
    --faint: #dfe6f0;
  }
  * { box-sizing: border-box; margin: 0; padding: 0; }
  html, body { width: 1200px; height: 843px; overflow: hidden; }
  body {
    background: var(--page-bg);
    font-family: "Open Sans", sans-serif;
    color: var(--ink);
    position: relative;
  }
  .card {
    position: absolute;
    width: 560px;
    height: 320px;
    background: linear-gradient(160deg, var(--card-white) 55%, var(--card-shade) 100%);
    box-shadow: 0 8px 24px rgba(0,0,0,0.18);
    overflow: hidden;
  }

  /* ---------- Appointment side ---------- */
  .card-back { left: 40px; top: 70px; }
  .back-mark {
    position: absolute; left: 40px; top: 40px;
    width: 150px; height: 150px; border-radius: 50%;
    background: var(--faint); opacity: 0.6;
  }
  .back-title {
    position: absolute; right: 40px; top: 26px;
    color: var(--brand-blue); font-weight: 700; font-size: 22px;
  }
  .title-rule {
    position: absolute; left: 40px; right: 40px; top: 62px;
    border-top: 2px dotted var(--rule);
  }
  .form-row {
    position: absolute; left: 40px; right: 40px;
    display: flex; align-items: flex-end; gap: 8px;
    color: var(--brand-blue); font-size: 16px;
  }
  .form-row .label { white-space: nowrap; }
  .form-row .line { flex: 1; border-bottom: 2px dotted var(--rule); height: 18px; }
  .form-row .ampm { font-size: 11px; align-self: flex-start; }
  .row-name { top: 86px; }
  .row-date { top: 126px; }
  .row-days { top: 166px; gap: 16px; font-size: 15px; }
  .day { display: flex; align-items: center; gap: 5px; }
  .box { width: 15px; height: 13px; border: 1.5px solid var(--ink); background: var(--card-white); }
  .row-note { top: 206px; }
  .row-extra { top: 244px; }
  .back-footer {
    position: absolute; left: 40px; right: 40px; bottom: 26px;
    text-align: center; font-size: 11px; color: var(--ink);
    white-space: nowrap;
  }

  /* ---------- Contact side ---------- */
  .card-front { left: 600px; top: 470px; }
  .brand {
    position: absolute; left: 30px; top: 38px;
    display: flex; align-items: center; gap: 12px;
  }
  .brand-dot { width: 40px; height: 40px; border-radius: 50%; background: var(--sky-blue); }
  .brand-name { color: var(--brand-blue); font-weight: 700; font-size: 26px; line-height: 1.05; }
  .contact {
    position: absolute; left: 30px; top: 120px;
    font-size: 14px; line-height: 22px; color: var(--ink);
    list-style: none;
  }
  .contact li { display: flex; align-items: center; gap: 8px; }
  .contact svg { width: 13px; height: 13px; fill: var(--brand-blue); flex: none; }
  .person {
    position: absolute; right: 44px; bottom: 40px; text-align: right;
  }
  .person-name { color: var(--brand-blue); font-weight: 700; font-size: 20px; }
  .person-role { font-size: 14px; color: var(--ink); }
  .edge-bar {
    position: absolute; right: 0; bottom: 40px;
    width: 12px; height: 46px; background: var(--brand-blue);
  }
</style>
</head>
<body>

<section class="card card-back" aria-label="Appointment card">
  <div class="back-mark"></div>
  <h2 class="back-title">Next Appointment</h2>
  <div class="title-rule"></div>

  <div class="form-row row-name">
    <span class="label">Name :</span><span class="line"></span>
    <span class="label">Time :</span><span class="line" style="flex:0 0 150px"></span>
    <span class="ampm">AM/PM</span>
  </div>
  <div class="form-row row-date">
    <span class="label">Date :</span><span class="line"></span>
  </div>
  <div class="form-row row-days">
    <span class="day">Sun <span class="box"></span></span>
    <span class="day">Mon <span class="box"></span></span>
    <span class="day">Tue <span class="box"></span></span>
    <span class="day">Wed <span class="box"></span></span>
    <span class="day">Thu <span class="box"></span></span>
    <span class="day">Fri <span class="box"></span></span>
    <span class="day">Sat <span class="box"></span></span>
  </div>
  <div class="form-row row-note">
    <span class="label">Note :</span><span class="line"></span>
  </div>
  <div class="form-row row-extra">
    <span class="line"></span>
  </div>
  <p class="back-footer">Please give me 24 hours notice if you are unable to keep this appointment.</p>
</section>

<section class="card card-front" aria-label="Contact card">
  <div class="brand">
    <span class="brand-dot"></span>
    <span class="brand-name">Harbourline<br>Physiotherapy</span>
  </div>

  <ul class="contact">
    <li>58 Wexley Lane Marrowdale</li>
    <li>NSW 2784</li>
    <li>
      <svg viewBox="0 0 24 24" aria-hidden="true"><path d="M6.6 10.8a15 15 0 0 0 6.6 6.6l2.2-2.2a1 1 0 0 1 1-.25 11.4 11.4 0 0 0 3.6.57 1 1 0 0 1 1 1V20a1 1 0 0 1-1 1A17 17 0 0 1 3 4a1 1 0 0 1 1-1h3.5a1 1 0 0 1 1 1c0 1.25.2 2.45.57 3.6a1 1 0 0 1-.25 1z"/></svg>
      02 9481 2057
    </li>
    <li>
      <svg viewBox="0 0 24 24" aria-hidden="true"><path d="M6 2h12v6H6zM4 9h16a2 2 0 0 1 2 2v6h-4v5H6v-5H2v-6a2 2 0 0 1 2-2zm4 8v3h8v-3z"/></svg>
      02 9481 2057
    </li>
    <li>
      <svg viewBox="0 0 24 24" aria-hidden="true"><path d="M2 5h20v14H2zm2 2v.5l8 5 8-5V7z"/></svg>
      info@harbourlinephysio.example.com.au
    </li>
    <li>
      <svg viewBox="0 0 24 24" aria-hidden="true"><circle cx="12" cy="12" r="10"/></svg>
      www.harbourlinephysio.example.com.au
    </li>
  </ul>

  <div class="person">
    <p class="person-name">Daniel Hartley</p>
    <p class="person-role">CEO/Founder</p>
  </div>
  <div class="edge-bar"></div>
</section>

</body>
</html>
```